Business cards for a fun web development agency

Hi,I am building a web development agency. You can read about it on the website http://kite-loft.examplehost.com. Basically, I want to focus on free and open source products and stay as far away from the corporate business feeling as possible. I want to build a community so I want the business card to feel fun and approachable (at the risk of professional if need be). I am uploading some of my image assets in various file formats. Feel free to use them or make your own if you want just keeping in theme with the website.
Industry/Entity Type
Building
Contact Information for Business Card
Company Name: Boat ShedWebsite: www.kiteloftdev.example (it's currently in alpha on http://kite-loft.examplehost.com if you want to see the them we are trying to capture)My name is: Banner B. SchaferMy email: banner@boatsheddev.comMy phone: 0431 587 904
Look and feel

```html
<!DOCTYPE html>
<html lang="en">
<head>
<meta charset="utf-8">
<title>Kite Loft business cards</title>
<link rel="stylesheet" href="https://fonts.googleapis.com/css2?family=Didact+Gothic&display=swap">
<style>
  :root {
    --page: #e9ecef;
    --ink: #1d2226;
    --ink-soft: #2c3338;
    --pale: #eef2fb;
    --mist: #b9cdea;
    --sky: #7fbfe0;
    --teal: #1ea6c9;
    --deep: #1478a8;
    --edge: #0f6b93;
  }
  html, body {
    margin: 0;
    padding: 0;
    width: 1200px;
    height: 892px;
    overflow: hidden;
    background: var(--page);
  }
  body {
    font-family: "Didact Gothic", "Helvetica Neue", Arial, sans-serif;
    color: var(--ink);
    position: relative;
  }
  .card {
    position: absolute;
    left: 250px;
    width: 700px;
    height: 400px;
    overflow: hidden;
    border-radius: 3px;
    box-shadow: 0 2px 0 var(--edge), 0 10px 24px rgba(20, 60, 90, 0.18);
  }
  .card--front { top: 31px; }
  .card--back  { top: 461px; }

  .card__surface {
    position: absolute;
    inset: 0;
  }
  .card--front .card__surface {
    background:
      radial-gradient(ellipse at 82% 20%, var(--teal) 0%, rgba(30,166,201,0) 55%),
      linear-gradient(20deg, var(--pale) 0%, var(--mist) 38%, var(--sky) 60%, var(--teal) 82%, var(--deep) 100%);
  }
  .card--back .card__surface {
    background:
      radial-gradient(ellipse at 78% 85%, var(--deep) 0%, rgba(20,120,168,0) 55%),
      linear-gradient(200deg, var(--pale) 0%, var(--mist) 30%, var(--sky) 55%, var(--teal) 80%, var(--deep) 100%);
  }

  .wordmark {
    position: absolute;
    margin: 0;
    font-weight: 400;
    color: var(--ink);
    line-height: 1;
    white-space: nowrap;
  }
  .card--front .wordmark {
    left: 48px;
    top: 112px;
    font-size: 64px;
  }
  .card--back .wordmark {
    left: 0;
    right: 0;
    top: 158px;
    text-align: center;
    font-size: 84px;
  }

  .rule {
    position: absolute;
    left: 380px;
    right: 0;
    top: 168px;
    height: 1.5px;
    background: var(--ink);
  }

  .holder {
    position: absolute;
    left: 126px;
    top: 200px;
    margin: 0;
    font-size: 29px;
    font-weight: 400;
    color: var(--ink-soft);
  }

  .contacts {
    position: absolute;
    left: 190px;
    top: 256px;
    margin: 0;
    padding: 0;
    list-style: none;
    font-size: 18px;
    color: var(--ink-soft);
  }
  .contacts__item {
    display: flex;
    align-items: center;
    gap: 12px;
    height: 30px;
  }
  .contacts__icon {
    width: 14px;
    height: 14px;
    flex: none;
    fill: var(--ink);
  }
</style>
</head>
<body>

<section class="card card--front" aria-label="Business card front">
  <div class="card__surface" role="img" aria-label="Low-poly faceted gradient from pale white-blue to teal"></div>

  <p class="wordmark">Kite Loft</p>
  <div class="rule"></div>

  <h1 class="holder">Corwin T. Aldous</h1>

  <ul class="contacts">
    <li class="contacts__item">
      <svg class="contacts__icon" viewBox="0 0 16 16" aria-hidden="true">
        <path d="M3.6 1.2 6 3.8 4.8 5.6c.9 2 2.6 3.7 4.6 4.6l1.8-1.2 2.6 2.4-1.4 2.6C7.4 13.8 2.2 8.6 1 3.6z"/>
      </svg>
      <span>0431 587 904</span>
    </li>
    <li class="contacts__item">
      <svg class="contacts__icon" viewBox="0 0 16 16" aria-hidden="true">
        <circle cx="8" cy="8" r="6.5" fill="none" stroke="#1d2226" stroke-width="1.6"/>
        <path d="M1.5 8h13M8 1.5c-3 3.5-3 9.5 0 13M8 1.5c3 3.5 3 9.5 0 13" fill="none" stroke="#1d2226" stroke-width="1.2"/>
      </svg>
      <span>www.kiteloftdev.example</span>
    </li>
    <li class="contacts__item">
      <svg class="contacts__icon" viewBox="0 0 16 16" aria-hidden="true">
        <path d="M1 3h14v10H1z"/>
        <path d="M1 3.5 8 9l7-5.5" fill="none" stroke="#eef2fb" stroke-width="1.3"/>
      </svg>
      <span>corwin@kiteloftdev.example</span>
    </li>
  </ul>
</section>

<section class="card card--back" aria-label="Business card back">
  <div class="card__surface" role="img" aria-label="Low-poly faceted gradient from pale lavender-blue to deep teal"></div>

  <p class="wordmark">Kite Loft</p>
</section>

</body>
</html>
```